Generate website for parcelnook.com

Please design a website for our business. It must be clean, streamlined and obvious.

Our business combines ecommerce, with social networking, and zorvi maps. The logo is a shopping bag (ecommerce) and honeycombs inside representing the various compartments of business that are offered throughout site.

Clients use our site to visit the interior of stores and restaurants through video streaming and can virtually "walk through" the store and purchase items with friends and loved ones through the web.

We want to incorporate this logo with the work that we are doing and play on this honeycomb theme.

Our business is "parcelnook.com" because we are all about "u"!

Please make homepage with about us tab, contact us form, mission tab, we also want a page with our research links included that bolster the case for our startup.

We will incorporate a small video on the front screen. A homepage like fildrawer.com only this time with our parcelnook!

Also include, COMING SOON, on the homepage please.
Updates

These are some good templates/example sites of clean and simple but effective: https://7elmrow.com/preview www.fildrawer.com

We are excited to see your submissions. Currently, a very good and only one designer has posted so far. Let us know!

Please include the TM (trademark) symbol after the logo, the name, and the slogan throughout the website. Thank you!

Put the TM after the LOGO and after the slogan "Placement ran Supreme" Lorcan

Target Market(s)

We will begin with female online shoppers.

Industry/Entity Type

Shopping

Font styles to use
Serif
Sans Serif

Colors
e567a6
fece3e
85cae6

Requirements
Must have
• Clean Look
Simple like Fildrawer with simple options "see film" or login/signup.

With browser tabs at the bottom much like fildrawer.

1. Shopper when opening Parcelnook.com website will see a simple webpage with a large Parcelnook logo in the center.

2. User will see log-in and password or create account in upper right hand corner of webpage. Mobile device website will be underneath logo.

3.We Prefer a background for webpages adding a softer experience on the the eyes of the user. A photo in the background to show shopretail experience.

4. Clicking on theParcelnook logo will inform users of details and instructions about platform. Example: About, contact, mission, Help etc. Logo will become somewhat like an interactive tool for help and guidance.

5. Parcelnook is currently scouting for it's founding venues. A founding venue will be the first venues to appear to the public on the Parcelnook platform. Founding venues (FV) will inherit a lifetime of the lowest possible rates of 2%* for the duration of it's business. All businesses wishing to participate in the founding venues offer please leave your email address and store name and a representative will get back with you.

*Venues will be subjected to credit card and CoinTrail rates in addition.

Nice to have
• http://www.zorvi.com/patents/US5193774

Must include the link above/visual of this page on the site as well.

```html
<!DOCTYPE html>
<html lang="en">
<head>
<meta charset="utf-8">
<title>Parcelnook — Coming Soon</title>
<link rel="stylesheet" href="https://fonts.googleapis.com/css2?family=Courgette&family=Arimo:wght@400;700&display=swap">
<style>
  :root {
    --black: #000000;
    --white: #ffffff;
    --pink: #e567a6;
    --pink-deep: #dd5a9c;
    --gold-light: #f0e08a;
    --gold: #c9ac3c;
    --gold-dark: #9a8228;
    --sky: #85cae6;
    --panel-blue: rgba(40, 120, 190, 0.55);
    --panel-blue-deep: rgba(10, 40, 110, 0.55);
    --mauve: #6e3e58;
    --rule: #8aa4a0;
    --logo-grey: #4d4d4f;
  }
  * { margin: 0; padding: 0; box-sizing: border-box; }
  html, body { width: 1200px; height: 1091px; overflow: hidden; background: var(--black); }
  .page { position: relative; width: 1200px; height: 1091px; overflow: hidden; }

  .top-bar { position: absolute; left: 0; top: 0; width: 1200px; height: 132px; background: var(--black); }
  .coming-soon {
    position: absolute; right: 40px; top: 42px;
    font-family: "Courgette", cursive; font-size: 46px; color: var(--white);
    letter-spacing: 2px; line-height: 1;
  }
  .coming-soon-rule { position: absolute; left: 750px; top: 104px; width: 450px; height: 1px; background: #9a9a9a; }

  .hero-photo {
    position: absolute; left: 0; top: 132px; width: 1200px; height: 560px;
    background:
      radial-gradient(ellipse 260px 90px at 760px 130px, rgba(230, 90, 200, 0.55), transparent 70%),
      radial-gradient(ellipse 180px 260px at 80px 330px, rgba(220, 40, 110, 0.75), transparent 75%),
      linear-gradient(180deg, #cfc5bf 0%, #8f8580 30%, #5d5350 58%, #9d8f88 82%, #c7bcb4 100%);
  }
  .bottom-band { position: absolute; left: 0; top: 692px; width: 1200px; height: 53px; background: var(--black); }

  .logo-area { position: absolute; left: 324px; top: 300px; display: flex; align-items: center; gap: 18px; }
  .logo-mark { width: 64px; height: 64px; background: var(--pink); }
  .logo-name {
    font-family: "Arimo", sans-serif; font-weight: 700; font-size: 78px;
    color: var(--logo-grey); line-height: 1;
  }
  .logo-tm { position: absolute; right: -26px; top: 0; font-family: "Arimo", sans-serif; font-size: 16px; color: var(--logo-grey); }

  .action-panel {
    position: absolute; left: 211px; top: 476px; width: 816px; height: 269px;
    background: linear-gradient(180deg, var(--panel-blue) 0%, var(--panel-blue-deep) 75%, rgba(0, 0, 0, 0.2) 100%);
  }
  .panel-divider { position: absolute; left: 416px; top: 13px; width: 2px; height: 240px; background: var(--white); }
  .action { position: absolute; top: 14px; width: 380px; text-align: center; }
  .action.signup { left: -14px; }
  .action.shop { left: 450px; }
  .action-title {
    font-family: "Courgette", cursive; font-size: 35px; line-height: 55px; color: var(--white);
  }
  .action-button {
    display: inline-block; margin-top: 20px; width: 207px; height: 58px;
    font-family: "Courgette", cursive; font-size: 30px; line-height: 52px; color: var(--white);
    text-decoration: none;
    background: linear-gradient(180deg, var(--gold-light) 0%, var(--gold) 45%, var(--gold-dark) 100%);
    border: 3px solid #8a96b0; box-shadow: 0 2px 3px rgba(0, 0, 0, 0.4);
  }
  .action.shop .action-button { margin-top: 20px; }

  .footer-strip { position: absolute; left: 0; top: 745px; width: 1200px; height: 15px; background: linear-gradient(90deg, var(--mauve), #7a5066 60%, #8c6a7c); }
  .footer {
    position: absolute; left: 0; top: 760px; width: 1200px; height: 331px;
    background: linear-gradient(155deg, #e89ac0 0%, var(--pink-deep) 20%, #ee9dc4 45%, #fbe5ef 68%, var(--white) 85%);
  }
  .footer-nav { position: absolute; left: 69px; top: 88px; width: 200px; list-style: none; text-align: center; }
  .footer-nav li { height: 59px; font-family: "Arimo", sans-serif; font-size: 26px; color: var(--white); }
  .footer-rule { position: absolute; left: 75px; top: 263px; width: 1020px; height: 1px; background: var(--rule); }
</style>
</head>
<body>
<div class="page">
  <header class="top-bar">
    <p class="coming-soon">COMING SOON</p>
    <div class="coming-soon-rule"></div>
  </header>

  <div class="hero-photo" role="img" aria-label="Photograph of a brightly lit clothing store entrance in a shopping mall with sale banners in the windows"></div>
  <div class="bottom-band"></div>

  <div class="logo-area">
    <div class="logo-mark"></div>
    <span class="logo-name">Parcelnook</span>
  </div>

  <section class="action-panel">
    <div class="panel-divider"></div>
    <div class="action signup">
      <h2 class="action-title">Sign up to join the<br>experience</h2>
      <a class="action-button" href="#">Signup/Login</a>
    </div>
    <div class="action shop">
      <h2 class="action-title">Want to<br>visit a shop</h2>
      <a class="action-button" href="#">Select a shop</a>
    </div>
  </section>

  <div class="footer-strip"></div>
  <footer class="footer">
    <ul class="footer-nav">
      <li>About us</li>
      <li>mission</li>
      <li>Contact us</li>
    </ul>
    <div class="footer-rule"></div>
  </footer>
</div>
</body>
</html>
```